VFX Company Business Card Design Project

The Kestrel Works is a decentralized Visual Effects Studio servicing the television and feature film industries.
Project Brief:
Take our logo that was previously designed on Pencil Harbor and make a double sided business card.
Requirements:
- Card MUST be double sided.
- Front of card MUST have the yellow part of our logo against the dark grey background.
- Back of card is completely up to the designer.
- Back of card must include the complete company logo.
Please follow these File Preparation guidelines:
http://printnook.ca/infopage?file=filetype_en&s=PrintNook_new&lang=en
Business

```html
<!DOCTYPE html>
<html lang="en">
<head>
<meta charset="utf-8">
<title>The Kestrel Works – Business Card</title>
<link href="https://fonts.googleapis.com/css2?family=Ubuntu:wght@400;500&display=swap" rel="stylesheet">
<style>
  :root {
    --backdrop: #d9d9d9;
    --card: #3a3a3a;
    --card-edge: #2e2e2e;
    --yellow: #e2b62a;
    --text-light: #e6e6e6;
  }
  * { margin: 0; padding: 0; box-sizing: border-box; }
  html, body {
    width: 1200px;
    height: 747px;
    overflow: hidden;
    background: var(--backdrop);
    font-family: "Ubuntu", sans-serif;
  }
  .stage {
    position: relative;
    width: 1200px;
    height: 747px;
  }
  .card {
    position: absolute;
    top: 64px;
    width: 354px;
    height: 620px;
    background: var(--card);
    border-radius: 4px;
    box-shadow: 0 2px 0 var(--card-edge), 0 10px 24px rgba(0,0,0,0.25);
    overflow: hidden;
  }
  .card--front { left: 212px; }
  .card--back { left: 634px; }

  /* Front */
  .front-mark {
    position: absolute;
    left: 50%;
    top: 50%;
    width: 520px;
    transform: translate(-50%, -50%) rotate(-90deg);
    display: flex;
    align-items: center;
    justify-content: center;
    gap: 22px;
  }
  .front-mark__dot {
    width: 34px;
    height: 34px;
    border-radius: 50%;
    background: var(--yellow);
    flex: none;
  }
  .front-mark__name {
    color: var(--yellow);
    font-weight: 500;
    font-size: 40px;
    letter-spacing: 1px;
    white-space: nowrap;
  }

  /* Back */
  .back-content {
    position: absolute;
    left: 34px;
    right: 34px;
    top: 58px;
  }
  .person {
    display: flex;
    align-items: baseline;
    gap: 8px;
    padding-bottom: 14px;
    border-bottom: 2px solid var(--yellow);
  }
  .person__name {
    color: var(--yellow);
    font-size: 24px;
    font-weight: 400;
    letter-spacing: 0.5px;
  }
  .person__role {
    color: var(--text-light);
    font-size: 15px;
  }
  .contacts {
    list-style: none;
    padding: 16px 0 14px;
    border-bottom: 2px solid var(--yellow);
  }
  .contacts li {
    display: flex;
    gap: 16px;
    font-size: 18px;
    line-height: 26px;
    color: var(--text-light);
  }
  .contacts__key {
    color: var(--yellow);
    width: 12px;
    font-size: 16px;
  }
  .address {
    padding-top: 22px;
    font-style: normal;
    font-size: 19px;
    line-height: 26px;
    color: var(--text-light);
  }
  .back-mark {
    position: absolute;
    left: 34px;
    bottom: 52px;
    display: flex;
    align-items: center;
    gap: 14px;
  }
  .back-mark__dot {
    width: 28px;
    height: 28px;
    border-radius: 50%;
    background: var(--yellow);
  }
  .back-mark__name {
    color: var(--yellow);
    font-weight: 500;
    font-size: 30px;
    white-space: nowrap;
  }
</style>
</head>
<body>
  <main class="stage">
    <section class="card card--front" aria-label="Card front">
      <div class="front-mark">
        <span class="front-mark__dot"></span>
        <span class="front-mark__name">The Kestrel Works</span>
      </div>
    </section>

    <section class="card card--back" aria-label="Card back">
      <div class="back-content">
        <div class="person">
          <span class="person__name">MARA LINDQVIST</span>
          <span class="person__role">| Managing Partner</span>
        </div>
        <ul class="contacts">
          <li><span class="contacts__key">t</span>(480) 555-0147</li>
          <li><span class="contacts__key">e</span>name@kestrelworks.com</li>
          <li><span class="contacts__key">w</span>www.kestrelworks.com</li>
        </ul>
        <address class="address">
          2150 East Mesa Vista Road,<br>
          Suite 410, Tempe,<br>
          Arizona 85281
        </address>
      </div>
      <div class="back-mark">
        <span class="back-mark__dot"></span>
        <span class="back-mark__name">The Kestrel Works</span>
      </div>
    </section>
  </main>
</body>
</html>
```